Market Research firm needs updated business cards with new logo

We need the logo to be included somewhere on the card (attached). We would also like the phrases "Independent, Objective, Comprehensive" and "Research You Can Trust" somewhere on the card. Front or back. Our colors are hex codes 6075a7, e48d25 and 5a5b5b. Though you are certainly not limited to those shades, whatever you produce should coordinate with them. I have also attached our favicon. Feel free to use it in your design, but please do not use it to replace the full logo.

Contact Information for Business Card

see project description

Font styles to use
Other font styles liked:
• Open Sans

Requirements
Must have
• the logo
• We use Open Sans font

```html
<!DOCTYPE html>
<html lang="en">
<head>
<meta charset="utf-8">
<title>Veritas Insight – Business Cards</title>
<link href="https://fonts.googleapis.com/css2?family=Open+Sans:wght@400;600&family=Roboto:wght@300;700&family=Tinos&display=swap" rel="stylesheet">
<style>
  :root {
    --bg: #c9c9c9;
    --orange: #e48d25;
    --orange-deep: #df7a1e;
    --orange-light: #eaa52e;
    --slate: #5a5b5b;
    --slate-dark: #474848;
    --brand-blue: #6075a7;
    --ink: #3a3a3a;
    --white: #ffffff;
  }
  * { box-sizing: border-box; margin: 0; padding: 0; }
  html, body { width: 1200px; height: 900px; overflow: hidden; }
  body {
    background: radial-gradient(circle at 50% 40%, #e2e2e2, var(--bg));
    font-family: "Open Sans", sans-serif;
    position: relative;
  }
  .card {
    position: absolute;
    width: 560px;
    height: 320px;
    border-radius: 18px;
    overflow: hidden;
    background: var(--white);
    box-shadow: 0 8px 22px rgba(0,0,0,.22);
  }
  .card-front { left: 60px; top: 80px; }
  .card-back { left: 580px; top: 500px; }
  .card svg.shapes { position: absolute; inset: 0; }

  .wordmark {
    position: absolute;
    display: flex;
    align-items: center;
    gap: 10px;
    font-family: "Open Sans", sans-serif;
    font-weight: 600;
    color: var(--orange);
    white-space: nowrap;
  }
  .wordmark .mark {
    border-radius: 50%;
    background: var(--orange);
    flex: none;
  }
  .card-front .wordmark { left: 0; right: 0; top: 138px; justify-content: center; font-size: 38px; }
  .card-front .wordmark .mark { width: 30px; height: 30px; }
  .card-back .wordmark { left: 38px; top: 112px; font-size: 24px; }
  .card-back .wordmark .mark { width: 20px; height: 20px; }

  .tagline {
    position: absolute;
    right: 40px;
    top: 24px;
    text-align: right;
    font-family: "Tinos", serif;
    font-size: 14px;
    line-height: 1.25;
    color: var(--ink);
  }
  .person {
    position: absolute;
    left: 42px;
    top: 236px;
    padding-left: 14px;
    border-left: 5px solid var(--orange);
    font-family: "Roboto", sans-serif;
    color: var(--white);
  }
  .person .name { font-weight: 700; font-size: 24px; letter-spacing: .5px; line-height: 1.05; }
  .person .role { font-weight: 300; font-size: 14px; letter-spacing: .5px; color: #e6e6e6; }

  .contact {
    position: absolute;
    right: 0;
    height: 46px;
    background: var(--orange);
    display: flex;
    align-items: center;
    gap: 14px;
    padding-left: 10px;
    color: var(--white);
    font-size: 11.5px;
    line-height: 1.3;
  }
  .contact-phone { top: 112px; width: 262px; }
  .contact-web { top: 168px; width: 232px; }
  .contact-address { top: 224px; width: 202px; }
  .contact .icon {
    width: 30px; height: 30px; border-radius: 50%;
    background: var(--orange);
    border: 2px solid #f4c48a;
    box-shadow: 0 2px 4px rgba(0,0,0,.3);
    display: flex; align-items: center; justify-content: center;
    flex: none;
  }
</style>
</head>
<body>

<section class="card card-front" aria-label="Card front">
  <svg class="shapes" width="560" height="320" viewBox="0 0 560 320">
    <defs>
      <linearGradient id="frontOrange" x1="0" y1="0" x2="1" y2="1">
        <stop offset="0" stop-color="#df7a1e"/>
        <stop offset="0.6" stop-color="#eaa52e"/>
        <stop offset="1" stop-color="#e48d25"/>
      </linearGradient>
    </defs>
    <rect width="560" height="320" fill="url(#frontOrange)"/>
    <polygon points="0,98 560,62 560,222 0,258" fill="#ffffff"/>
  </svg>
  <div class="wordmark"><span class="mark"></span>Veritas Insight</div>
</section>

<section class="card card-back" aria-label="Card back">
  <svg class="shapes" width="560" height="320" viewBox="0 0 560 320">
    <polygon points="0,205 560,98 560,320 0,320" fill="#5a5b5b"/>
    <polygon points="270,152 560,98 560,112 300,160" fill="#474848"/>
  </svg>

  <p class="tagline">Independent, Objective<br>Comprehensive and<br>Research You Can Trust</p>

  <div class="wordmark"><span class="mark"></span>Veritas Insight</div>

  <div class="person">
    <p class="name">MARLON KEANE</p>
    <p class="role">SOLUTION MANAGER</p>
  </div>

  <div class="contact contact-phone">
    <span class="icon"><svg width="14" height="14" viewBox="0 0 24 24"><path fill="#fff" d="M6.6 10.8a15 15 0 0 0 6.6 6.6l2.2-2.2c.3-.3.7-.4 1-.2 1.1.4 2.3.6 3.6.6.6 0 1 .4 1 1V20c0 .6-.4 1-1 1A17 17 0 0 1 3 4c0-.6.4-1 1-1h3.5c.6 0 1 .4 1 1 0 1.3.2 2.5.6 3.6.1.3 0 .7-.2 1z"/></svg></span>
    <span>+15550142876<br>+15550193421</span>
  </div>
  <div class="contact contact-web">
    <span class="icon"><svg width="15" height="15" viewBox="0 0 24 24" fill="none" stroke="#fff" stroke-width="2"><circle cx="12" cy="12" r="9"/><path d="M3 12h18M12 3c3 3 3 15 0 18M12 3c-3 3-3 15 0 18"/></svg></span>
    <span>www.northfieldstudio.com<br>www.northfield.com</span>
  </div>
  <div class="contact contact-address">
    <span class="icon"><svg width="13" height="15" viewBox="0 0 24 24"><path fill="#fff" d="M12 2a7 7 0 0 0-7 7c0 5 7 13 7 13s7-8 7-13a7 7 0 0 0-7-7zm0 9.5A2.5 2.5 0 1 1 12 6.5a2.5 2.5 0 0 1 0 5z"/></svg></span>
    <span>Harbor Lane, Eastbrook<br>City</span>
  </div>
</section>

</body>
</html>
```